Etiketten-Design für einen importierten Honig
Zielgruppe
Wir importieren originalen Manuka Honig aus Neuseeland. Der Manuka Honig ist bekannt für seine besonderen Eigenschaften (antibakteriell, etc.). Ein Glas unseres Honigs (500g) kostet zwischen 30 und 150 EUR.
Unsere Zielgruppe sind gesundheitsbewusste Kunden, die wenig preissensibel sind. Überwiegend wird der Manuka Honig im Fachhandel (z.B. Reformhaus, Drogerie, Biomarkt, etc.) verkauft. Der Großteil unserer Kunden ist 30+ Jahre.
Aufgabenstellung
Bei dem Etikett handelt es sich um das erste Produktetikett. Damit ist in der Farbgestaltung noch alles offen. Das Logo und der Name ist jedoch fix.
Das Etikett ist wird auf einem bpa-freien schwarzen Plastikbehälter angebracht. Dieser ist bei Manuka Honigen Standard aufgrund des langen Transports von Neuseeland nach Deutschland (gerne googeln). Der Deckel dieses Behälters ist schwarz.
Nachdem es sich um ein hochpreisiges Produkt handelt, soll das Etikett diese hohe Wertigkeit widerspiegeln. Damit ist eine Veredelung des Etiketts notwendig. Viele Konkurrenten arbeiten mit Gold, alternative Farben sind jedoch auch möglich.
Das Etikett überdeckt drei der vier Seiten des Plastikbehälters (vorne + links + rechts). Die Maße sind 160 mm x 60 mm. Zusätzlich zu den Etikettenmaßen bitte 2 mm Beschnittzugabe je Seite hinzufügen.
Hintergrundinformationen zu unserer Marke:
- Der Markenname lautet Kalvio. Der Markenname leitet sich von der ersten Imkerin Neuseelands ab - Edith Carrow. Sie hatte im Jahr 1839 die ersten Bienenstöcke nach Neuseeland gebracht und den ersten Manuka Honig geerntet.
- Unser Logo ist eine Verbindung einer Frau und den neuseeländischen Farn. Dieses Logo stellt also direkt eine Verbindung zu Neuseeland dar.
- Unsere Marke Kalvio ist eine qualitativ hochwertige, luxuriöse und hochpreisige Marke. Genau wie in dem Logo selbst, sollen diese Verbindungen zu Neuseeland, der Natur (Honig ist ein Naturprodukt) und Edith Carrow auch auf dem Etikett zu finden sein.
Wonach suchen wir:
- Wir sind auf der Suche nach einem einzigartigen Design, der unseren Honig besonders hervorhebt. Das Etikett soll auffällig sein und uns von anderen unterscheiden. (Eye-catching)
- Eine Veredelung des Etiketts ist Pflicht, da dies für uns die Wertigkeit des Etiketts und des Produktes stark erhöht. In welcher Art die Veredelung durchgeführt wird, ist Ihnen überlassen.
Das dürfen Sie frei wählen:
- Bisher haben..

```html
<!DOCTYPE html>
<html lang="de">
<head>
<meta charset="UTF-8">
<title>Kalvio Manuka Honig – Etikett</title>
<link rel="stylesheet" href="https://fonts.googleapis.com/css2?family=Roboto:wght@400;500;700&display=swap">
<style>
  :root {
    --backdrop: #743a3e;
    --label-deep: #141b1f;
    --label-mist: #2c3a40;
    --label-teal: #22343a;
    --copper: #c8906a;
    --copper-text: #b98548;
  }
  * { margin: 0; padding: 0; box-sizing: border-box; }
  html, body {
    width: 1200px;
    height: 1200px;
    overflow: hidden;
    background: var(--backdrop);
  }
  .canvas {
    position: relative;
    width: 1200px;
    height: 1200px;
    display: flex;
    align-items: center;
    justify-content: center;
  }
  .label {
    position: relative;
    width: 1040px;
    height: 917px;
    overflow: hidden;
    font-family: "Roboto", sans-serif;
  }
  .label__scene {
    position: absolute;
    inset: 0;
    background:
      radial-gradient(ellipse 70% 30% at 50% 62%, rgba(120,140,150,0.35), transparent 70%),
      linear-gradient(180deg, var(--label-mist) 0%, var(--label-deep) 30%, var(--label-teal) 55%, #1a2428 70%, #2a3a40 85%, var(--label-deep) 100%);
  }
  .label__mark {
    position: absolute;
    left: 50%;
    top: 70px;
    width: 390px;
    height: 390px;
    margin-left: -195px;
    border-radius: 50%;
    border: 6px solid var(--copper);
  }
  .label__name {
    position: absolute;
    left: 0;
    right: 0;
    top: 500px;
    text-align: center;
    font-size: 150px;
    font-weight: 500;
    line-height: 1;
    color: var(--copper);
  }
  .label__info {
    position: absolute;
    left: 0;
    right: 0;
    top: 712px;
    text-align: center;
    color: var(--copper-text);
    font-size: 39px;
    font-weight: 400;
    letter-spacing: 0.2em;
    line-height: 54px;
  }
  .label__info strong { font-weight: 700; }
  .label__weight {
    position: absolute;
    right: 50px;
    top: 820px;
    color: var(--copper-text);
    font-size: 39px;
    letter-spacing: 0.2em;
    line-height: 54px;
  }
</style>
</head>
<body>
<main class="canvas">
  <section class="label">
    <div class="label__scene" role="img" aria-label="Nebelige neuseeländische Berglandschaft mit schneebedeckten Gipfeln, die sich in einem See spiegeln"></div>
    <div class="label__mark"></div>
    <h1 class="label__name">Kalvio</h1>
    <p class="label__info">MANUKA HONIG<br>AUS NEUSEELAND<br>MGO <strong>450+</strong></p>
    <p class="label__weight">500G</p>
  </section>
</main>
</body>
</html>
```